Card Design for my dog training business Brightpaw Obedience

Need a business card design for my dog training business with my new logo. Want the card to come off professional yet fun. Want it to be very eye catchy as well. I normally have these at vet clinics, pet stores, and groomers. so need it to look better than my competitors.
Target Market(s)
dog owners
Industry/Entity Type
Dog Training
Contact Information for Business Card
needs logo, my name and info
Font styles to use
Serif
Colors
0255a3
ffffff
ec1f27
000000
333333
fbfbfb
Requirements
Must have
- Brightpaw Obedience
- Felix Orland
- 415 903 2276
- info@brightpawobedience.example
- www.brightpawobedience.example

```html
<!DOCTYPE html>
<html lang="en">
<head>
<meta charset="utf-8">
<title>Brightpaw Obedience – Business Card</title>
<link href="https://fonts.googleapis.com/css2?family=Cormorant+Garamond:ital,wght@0,500;0,600;1,500&family=Lato:wght@400&display=swap" rel="stylesheet">
<style>
  :root {
    --stage: #141414;
    --card: #262626;
    --card-edge: #303030;
    --white: #ffffff;
    --off-white: #fbfbfb;
    --red: #ec1f27;
    --emboss: #8a8a8a;
    --muted: #333333;
  }
  * { box-sizing: border-box; margin: 0; padding: 0; }
  html, body {
    width: 1200px; height: 900px; overflow: hidden;
    background: var(--stage);
  }
  .canvas {
    position: relative; width: 1200px; height: 900px;
    display: flex; flex-direction: column; align-items: center; justify-content: center; gap: 40px;
  }
  .card {
    position: relative; width: 700px; height: 400px;
    background: linear-gradient(160deg, var(--card-edge), var(--card));
    box-shadow: 0 18px 40px rgba(0,0,0,.6);
    overflow: hidden;
  }
  /* Front */
  .card-front { display: flex; align-items: center; justify-content: center; }
  .front-brand {
    font-family: "Cormorant Garamond", serif; font-weight: 600;
    font-size: 40px; letter-spacing: 2px; color: var(--emboss);
    text-align: center;
  }
  /* Back */
  .card-back { display: flex; align-items: center; }
  .back-brand-area {
    width: 330px; height: 100%;
    display: flex; flex-direction: column; align-items: center; justify-content: center; gap: 22px;
  }
  .back-brand {
    font-family: "Cormorant Garamond", serif; font-weight: 600;
    font-size: 34px; letter-spacing: 1px; color: var(--white); text-align: center; line-height: 1.1;
  }
  .tagline {
    font-family: "Cormorant Garamond", serif; font-style: italic; font-weight: 500;
    font-size: 14px; color: var(--off-white);
  }
  .divider { width: 2px; height: 200px; background: var(--red); flex: none; }
  .details { padding-left: 36px; padding-right: 20px; color: var(--white); font-family: "Lato", sans-serif; }
  .person-name {
    font-family: "Cormorant Garamond", serif; font-weight: 600;
    font-size: 26px; letter-spacing: 1.5px; color: var(--red); text-transform: uppercase;
  }
  .person-role { font-size: 19px; margin-bottom: 14px; }
  .address { font-size: 19px; line-height: 1.3; margin-bottom: 8px; }
  .contact-list { list-style: none; font-size: 18px; line-height: 1.55; }
  .contact-list li { display: flex; align-items: center; gap: 10px; white-space: nowrap; }
  .contact-list svg { width: 13px; height: 13px; flex: none; }
</style>
</head>
<body>
<main class="canvas">
  <section class="card card-front" aria-label="Card front">
    <div class="front-brand">Brightpaw Obedience</div>
  </section>

  <section class="card card-back" aria-label="Card back">
    <div class="back-brand-area">
      <div class="back-brand">Brightpaw<br>Obedience</div>
      <p class="tagline">“Calm dogs, happy homes, one lesson at a time.”</p>
    </div>
    <div class="divider"></div>
    <div class="details">
      <h1 class="person-name">Felix Orland</h1>
      <p class="person-role">Managing Director</p>
      <p class="address">120 Alder Lane,<br>Springfield, 8012</p>
      <ul class="contact-list">
        <li>
          <svg viewBox="0 0 16 16" aria-hidden="true"><path d="M4 1l3 3-2 2c1 2 3 4 5 5l2-2 3 3-2 2C7 14 2 9 2 3z" fill="var(--red)"/></svg>
          415 903 2276
        </li>
        <li>
          <svg viewBox="0 0 16 16" aria-hidden="true"><rect x="1.5" y="3.5" width="13" height="9" fill="none" stroke="var(--red)" stroke-width="1.5"/><path d="M1.5 3.5L8 9l6.5-5.5" fill="none" stroke="var(--red)" stroke-width="1.5"/></svg>
          info@brightpawobedience.example
        </li>
        <li>
          <svg viewBox="0 0 16 16" aria-hidden="true"><circle cx="8" cy="8" r="6.5" fill="none" stroke="var(--red)" stroke-width="1.4"/><ellipse cx="8" cy="8" rx="3" ry="6.5" fill="none" stroke="var(--red)" stroke-width="1.2"/><path d="M1.5 8h13" stroke="var(--red)" stroke-width="1.2"/></svg>
          www.brightpawobedience.example
        </li>
      </ul>
    </div>
  </section>
</main>
</body>
</html>
```